New Web Site Design - Tallow Ridge Communication Solutions

We are looking for a completely new web site design. Tallow Ridge Communication Solutions is a full service company providing PBX and IP/Cloud Based phone systems. We also sell and install video camera surveillance systems and provide low voltage cabling services (CAT5 and CAT3). We are looking for something professional looking. We want to be able to showcase our vendor partners as well as be able to show photos of some of the work we have done. We will also want to be able to post PDF brochures as well as make changes to the website ourselves.

Target Market(s)

Commercial

Industry/Entity Type

Communication

Coding

Coded - Design and coding required

Number of Pages Required

5+ page

Font styles to use
Sans Serif

Colors
0455a3

Requirements
Must have
• Ability to upload PDF brochures
• Professional look and feel
• Ability to upload and easily insert job photos
• Thinking it should have at least 6 pages: Main page, phone systems and services page, carrier services page, video surveillance systems and service page, low voltage cabling services page, contact us page

```html
<!DOCTYPE html>
<html lang="en">
<head>
<meta charset="utf-8">
<title>Tallow Ridge Communication Solutions</title>
<link href="https://fonts.googleapis.com/css2?family=Roboto:wght@400;500;700&family=Roboto+Condensed:wght@400;700&family=Roboto+Slab:wght@400&display=swap" rel="stylesheet">
<style>
:root{
  --brand:#0455a3;
  --brand-dark:#033f7a;
  --navy:#0b2a55;
  --ink:#222;
  --text:#444;
  --muted:#666;
  --panel:#efefef;
  --footer:#3c3c3c;
  --footer-bar:#7a7a7a;
  --white:#fff;
}
*{box-sizing:border-box;margin:0;padding:0}
html,body{width:1200px;height:2384px;overflow:hidden;background:var(--white)}
body{position:relative;font-family:"Roboto",Arial,sans-serif;color:var(--text)}
h1,h2,h3,h4{font-weight:400}
.abs{position:absolute}
a{color:var(--brand-dark);text-decoration:underline}

/* header */
.site-header{left:0;top:0;width:1200px;height:143px;background:var(--white)}
.header-band{right:0;top:0;width:83px;height:143px;background:var(--brand)}
.brand{left:82px;top:50px}
.brand-name{font-family:"Roboto",sans-serif;font-weight:400;font-size:28px;line-height:1.1;color:var(--navy);display:block;width:380px}
.follow{left:893px;top:20px;display:flex;align-items:center;gap:8px;font-size:13px;color:var(--ink)}
.follow span.dot{width:28px;height:28px;border-radius:50%;background:#333;display:inline-block}
.brochure{left:684px;top:72px;display:flex;align-items:center;gap:6px}
.brochure .btn{background:var(--brand);color:var(--white);font-family:"Roboto Condensed",sans-serif;font-size:17px;padding:0 14px;height:32px;line-height:32px}
.call{left:936px;top:80px;display:flex;align-items:center;gap:6px}
.call .label{font-size:13px;color:var(--ink);font-weight:500}
.call .num{font-size:21px;color:var(--brand);font-weight:500;line-height:1}

/* nav */
.main-nav{left:0;top:143px;width:1200px;height:52px;background:var(--brand);display:flex;align-items:center;padding-left:80px}
.main-nav a{font-family:"Roboto Slab",serif;color:var(--white);text-decoration:none;font-size:15px;padding:0 11px;height:52px;line-height:52px;border-right:1px solid rgba(255,255,255,.25)}
.main-nav a:last-child{border-right:none}

/* hero */
.hero{left:0;top:195px;width:1200px;height:447px;background:linear-gradient(100deg,#e9e6df 0%,#d8d6d0 30%,#6b6d70 55%,#3a3b3d 75%,#c9c9c9 100%)}
.hero-title{left:87px;top:312px;font-family:"Roboto Condensed",sans-serif;font-weight:400;font-size:42px;line-height:61px;color:#3a3a3a}
.hero-arrow{width:34px;height:34px;background:#333;top:400px}

/* sections */
.section-title{font-family:"Roboto Condensed",sans-serif;font-weight:400;font-size:28px;color:var(--ink);text-align:center;width:1200px;left:0}
.title-rule{height:4px;background:var(--brand);width:70px;left:565px}
.products{left:0;top:642px;width:1200px;height:426px;background:var(--panel)}
.lead{width:1200px;left:0;text-align:center;font-size:12px;color:var(--ink)}
.service{width:220px;text-align:center}
.service .icon{width:116px;height:116px;border-radius:50%;border:3px solid #333;margin:0 auto;background:var(--brand);display:flex;align-items:center;justify-content:center;box-shadow:inset 0 0 0 4px #fff}
.service h3{font-family:"Roboto Condensed",sans-serif;font-weight:400;font-size:18px;color:var(--ink);margin-top:14px}
.service p{font-size:12px;color:var(--muted);line-height:17px;margin-top:12px}
.service a{font-size:12px;display:inline-block;margin-top:9px}

.welcome-text{left:119px;top:1176px;width:962px;text-align:center;font-size:12px;line-height:21px;color:var(--ink)}
.welcome-text a{display:inline-block;margin-top:3px}

.tile{width:248px;height:230px;border:3px solid #c8c8c8;top:1420px}
.tile .photo{width:100%;height:100%}
.tile .cap{position:absolute;left:0;bottom:0;width:100%;height:40px;background:rgba(0,0,0,.8);color:var(--white);font-family:"Roboto Condensed",sans-serif;font-size:17px;text-align:center;line-height:40px}
.pager{top:1672px;width:26px;height:24px;border:1px solid #333;display:flex;align-items:center;justify-content:center;background:#fff}

.vendors{left:0;top:1743px;width:1200px;height:243px;background:var(--panel)}
.partner{top:1872px;height:66px;background:#cfcfcf}

/* footer */
.site-footer{left:0;top:1986px;width:1200px;height:359px;background:var(--footer)}
.footer-title{left:127px;top:2005px;font-family:"Roboto Condensed",sans-serif;font-weight:400;font-size:20px;color:var(--white);border-bottom:1px dashed #999;padding-bottom:4px}
.contact-item{left:100px;display:flex;gap:18px;color:var(--white);font-size:13px;line-height:19px}
.contact-item svg{width:18px;flex:none;margin-top:2px}
.footer-brand{left:480px;top:2150px;width:200px;text-align:center;font-size:22px;color:#9aa3ad;line-height:1.2}
.inquiry{left:774px;top:2005px;width:311px;height:325px;background:rgba(130,130,130,.55);border-top:3px solid #ddd;padding:16px 14px}
.inquiry h4{font-family:"Roboto Condensed",sans-serif;font-weight:400;font-size:26px;color:var(--white);display:flex;align-items:center;gap:12px}
.inquiry p{color:var(--white);font-size:12px;margin:14px 0 12px}
.field{height:33px;background:rgba(255,255,255,.18);margin-bottom:5px;color:#eee;font-size:12px;padding:9px 12px}
.field.msg{height:50px}
.submit{width:120px;height:34px;background:var(--brand);color:var(--white);font-weight:700;font-size:16px;text-align:center;line-height:34px;margin-top:6px}
.copyright{left:0;top:2345px;width:1200px;height:39px;background:var(--footer-bar);color:var(--white);font-size:12px;text-align:center;line-height:39px}
</style>
</head>
<body>

<header class="abs site-header">
  <div class="abs header-band"></div>
  <div class="abs brand"><span class="brand-name">Tallow Ridge Communication Solutions</span></div>
  <div class="abs follow">Follow Us On <span class="dot"></span><span class="dot"></span><span class="dot"></span></div>
  <div class="abs brochure">
    <svg width="40" height="46" viewBox="0 0 40 46"><rect x="4" y="2" width="30" height="40" fill="#fff" stroke="#0455a3" stroke-width="3"/><path d="M19 12v16m-7-7 7 7 7-7" stroke="#0455a3" stroke-width="3" fill="none"/></svg>
    <span class="btn">Download Our Brochure</span>
  </div>
  <div class="abs call">
    <svg width="30" height="30" viewBox="0 0 32 32"><circle cx="16" cy="16" r="14" fill="none" stroke="#0455a3" stroke-width="2.5"/><path d="M11 9c-2 2-1 7 4 12s10 6 12 4l-3-3-3 2c-2-1-5-4-6-6l2-3z" fill="#0455a3"/></svg>
    <div><div class="label">Call Us Today</div><div class="num">123-456-7890</div></div>
  </div>
</header>

<nav class="abs main-nav">
  <a>About Us</a><a>Phone Systems &amp; Services</a><a>Low Voltage Cabling Service</a><a>Carrier Services</a><a>Video Surveillance Systems Service</a><a>Contact Us</a>
</nav>

<section class="abs hero" role="img" aria-label="Office desk phone with a coiled handset cord on a bright desk"></section>
<h1 class="abs hero-title">Hosted PBX<br>The Business Phone<br>System in the Cloud</h1>
<svg class="abs hero-arrow" style="left:6px" viewBox="0 0 34 34"><path d="M20 10l-8 7 8 7z" fill="#fff"/></svg>
<svg class="abs hero-arrow" style="left:1154px" viewBox="0 0 34 34"><path d="M14 10l8 7-8 7z" fill="#fff"/></svg>

<section class="abs products"></section>
<h2 class="abs section-title" style="top:670px">Product &amp; Services</h2>
<p class="abs lead" style="top:709px">Lorem ipsum dolor sit amet, consectetur adipiscing elit. Aenean et dignissim sem,&nbsp; interdum risus. Vestibulum consectetur</p>
<div class="abs" style="left:258px;top:741px;width:684px;height:1px;background:#ccc"></div>
<div class="abs title-rule" style="top:740px"></div>

<div class="abs service" style="left:63px;top:780px">
  <div class="icon"><svg width="54" height="54" viewBox="0 0 54 54" fill="#fff"><rect x="6" y="10" width="10" height="36" rx="3"/><rect x="19" y="8" width="30" height="40" rx="3"/><rect x="24" y="13" width="20" height="8" fill="#0455a3"/><g fill="#0455a3"><rect x="24" y="25" width="5" height="5"/><rect x="31" y="25" width="5" height="5"/><rect x="38" y="25" width="5" height="5"/><rect x="24" y="33" width="5" height="5"/><rect x="31" y="33" width="5" height="5"/><rect x="38" y="33" width="5" height="5"/></g></svg></div>
  <h3>PBX Phone Systems</h3><p>Lorem ipsum dolr sit amet,<br>consectetur adipiscing elit.<br>Aenean et dign.</p><a>Read more</a>
</div>
<div class="abs service" style="left:275px;top:780px">
  <div class="icon"><svg width="60" height="50" viewBox="0 0 60 50"><path d="M12 38a10 10 0 0 1 2-20 14 14 0 0 1 27-3 11 11 0 0 1 7 23z" fill="none" stroke="#fff" stroke-width="2.5"/><rect x="20" y="22" width="20" height="14" rx="2" fill="#fff"/></svg></div>
  <h3>IP/Cloud Phone System</h3><p>Lorem ipsum dolr sit amet,<br>consectetur adipiscing elit.<br>Aenean et dign.</p><a>Read more</a>
</div>
<div class="abs service" style="left:500px;top:780px">
  <div class="icon"><svg width="60" height="44" viewBox="0 0 60 44" fill="#fff"><path d="M6 10l38 10-4 12L4 20z"/><rect x="44" y="20" width="4" height="18"/><rect x="40" y="36" width="14" height="4"/></svg></div>
  <h3>Video camera surveillance</h3><p>Lorem ipsum dolr sit amet,<br>consectetur adipiscing elit.<br>Aenean et dign.</p><a>Read more</a>
</div>
<div class="abs service" style="left:719px;top:780px">
  <div class="icon"><svg width="50" height="56" viewBox="0 0 50 56" fill="none" stroke="#fff" stroke-width="3"><rect x="14" y="14" width="20" height="34" rx="3"/><path d="M30 6a14 14 0 0 1 12 12M30 12a8 8 0 0 1 6 6"/></svg></div>
  <h3>Carrier Service</h3><p>Lorem ipsum dolr sit amet,<br>consectetur adipiscing elit.<br>Aenean et dign.</p><a>Read more</a>
</div>
<div class="abs service" style="left:920px;top:780px">
  <div class="icon"><svg width="56" height="56" viewBox="0 0 56 56" fill="none" stroke="#fff" stroke-width="2.5"><path d="M8 10c10 0 12 12 22 16M12 22c8 2 12 8 18 8"/><rect x="28" y="28" width="16" height="10" transform="rotate(35 36 33)" fill="#fff"/><path d="M42 40l8 8"/></svg></div>
  <h3>Low Voltage Cabling</h3><p>Lorem ipsum dolr sit amet,<br>consectetur adipiscing elit.<br>Aenean et dign.</p><a>Read more</a>
</div>

<h2 class="abs section-title" style="top:1113px">Welcome to Tallow Ridge Communications Solutions</h2>
<div class="abs" style="left:270px;top:1158px;width:660px;height:1px;background:#ccc"></div>
<div class="abs title-rule" style="left:536px;width:128px;top:1157px"></div>
<p class="abs welcome-text">Lorem ipsum dolor sit amet, consectetuer adipiscing elit, sed diam nonummy nibh euismod tincidunt ut laoreet dolore magna aliquam erat volutpat. Ut wisi enim ad minim veniam, quis nostrud exerci tation ullamcorper suscipit lobortis nisl ut aliquip ex ea commodo consequat. Duis autem vel eum iriure dolor in hendrerit in vulputate velit esse molestie consequat, vel illum dolore eu feugiat nulla facilisis at vero eros et accumsan et iusto odio dignissim qui blandit praesent luptatum zzril delenit augue duis dolore te feugait nulla facilisi.<br><a>Read more</a></p>
<div class="abs" style="left:260px;top:1316px;width:680px;height:3px;background:radial-gradient(ellipse at center,#ddd,transparent 70%)"></div>

<h2 class="abs section-title" style="top:1355px">Project Gallery</h2>
<div class="abs" style="left:505px;top:1392px;width:190px;height:1px;background:#ccc"></div>
<div class="abs title-rule" style="left:575px;width:50px;top:1391px"></div>

<div class="abs tile" style="left:83px"><div class="photo" role="img" aria-label="Desk phone on an office table" style="background:linear-gradient(160deg,#f4f4f4,#bdbdbd 55%,#333)"></div><div class="cap">Lorem Ispim is Dummmy</div></div>
<div class="abs tile" style="left:345px"><div class="photo" role="img" aria-label="Technician mounting a security camera under a blue sky" style="background:linear-gradient(150deg,#2c6fb5,#5c93cc 50%,#b88a70)"></div><div class="cap">Lorem Ispim is Dummmy</div></div>
<div class="abs tile" style="left:605px"><div class="photo" role="img" aria-label="Cabling installer in a hard hat holding cable" style="background:linear-gradient(160deg,#d9dde2,#8b96a3 50%,#27324a)"></div><div class="cap">Lorem Ispim is Dummmy</div></div>
<div class="abs tile" style="left:868px"><div class="photo" role="img" aria-label="Hands dialing a black office phone" style="background:linear-gradient(160deg,#e6edf2,#9aa6ae 50%,#222)"></div><div class="cap">Lorem Ispim is Dummmy</div></div>

<div class="abs pager" style="left:568px"><svg width="10" height="12"><path d="M8 1L2 6l6 5" stroke="#333" stroke-width="1.8" fill="none"/></svg></div>
<div class="abs pager" style="left:604px;border-color:var(--brand)"><svg width="10" height="12"><path d="M2 1l6 5-6 5" stroke="#0455a3" stroke-width="1.8" fill="none"/></svg></div>

<section class="abs vendors"></section>
<h2 class="abs section-title" style="top:1773px">Our Vendor Partners</h2>
<div class="abs" style="left:480px;top:1810px;width:240px;height:1px;background:#ccc"></div>
<div class="abs title-rule" style="left:568px;width:64px;top:1809px"></div>
<svg class="abs" style="left:58px;top:1890px" width="14" height="26"><path d="M12 2L2 13l10 11" stroke="#777" stroke-width="2" fill="none"/></svg>
<svg class="abs" style="left:1128px;top:1890px" width="14" height="26"><path d="M2 2l10 11-10 11" stroke="#777" stroke-width="2" fill="none"/></svg>
<div class="abs partner" style="left:98px;width:90px;border-radius:50%"></div>
<div class="abs partner" style="left:230px;width:140px"></div>
<div class="abs partner" style="left:394px;width:104px"></div>
<div class="abs partner" style="left:522px;width:104px"></div>
<div class="abs partner" style="left:650px;width:134px"></div>
<div class="abs partner" style="left:804px;width:176px"></div>
<div class="abs partner" style="left:1002px;width:104px"></div>

<footer class="abs site-footer" role="img" aria-label="Faint street map behind the footer"></footer>
<h3 class="abs footer-title">Contact Information</h3>
<div class="abs contact-item" style="top:2050px"><svg viewBox="0 0 18 22" height="22"><path d="M9 1a7 7 0 0 1 7 7c0 5-7 13-7 13S2 13 2 8a7 7 0 0 1 7-7z" fill="#fff"/><circle cx="9" cy="8" r="2.5" fill="#3c3c3c"/></svg><div>Postal Address<br>Street Name, City Name State Zipcode</div></div>
<div class="abs contact-item" style="top:2106px"><svg viewBox="0 0 18 18" height="18"><path d="M3 2c-2 2-1 6 4 10s8 5 10 3l-3-3-2 2c-2-1-4-3-5-5l2-2z" fill="#fff"/></svg><div>Telephone<br>123-456-7890 &amp; Fax: 456-789-4560</div></div>
<div class="abs contact-item" style="top:2162px"><svg viewBox="0 0 18 14" height="14"><rect x="1" y="1" width="16" height="12" fill="#fff"/><path d="M1 1l8 6 8-6" stroke="#3c3c3c" fill="none"/></svg><div>Email<br>Information and Support: inquiry@tallowridge.com</div></div>
<div class="abs contact-item" style="top:2218px"><svg viewBox="0 0 18 18" height="18"><rect x="3" y="3" width="12" height="12" fill="#fff"/></svg><div>Social Page<br>www.socialpage.example/tallowridge</div></div>
<div class="abs contact-item" style="top:2273px"><svg viewBox="0 0 18 18" height="18"><rect x="3" y="3" width="12" height="12" fill="#fff"/></svg><div>Photo Stream<br>www.photostream.example/tallowridge</div></div>

<div class="abs footer-brand">Tallow Ridge<br>Communication Solutions</div>

<form class="abs inquiry">
  <h4><svg width="38" height="38" viewBox="0 0 38 38"><circle cx="19" cy="19" r="18" fill="#fff"/><path d="M12 10c-2 2-1 7 4 12s10 6 12 4l-3-3-3 2c-2-1-5-4-6-6l2-3z" fill="#0455a3"/></svg>Quick Inquiry</h4>
  <p>Lorem ipsum dolor sit amet, consectetuer</p>
  <div class="field">Name</div>
  <div class="field">Email</div>
  <div class="field">Phone</div>
  <div class="field msg">Message</div>
  <div class="submit">SUBMIT</div>
</form>

<div class="abs copyright">© 2015&nbsp; TallowRidgeCommunicationSolutions&nbsp; All rights reserved</div>
</body>
</html>
```